CBD PATCHES

Design creation of my CBD patch box.
Product must look Pharamaceutical grade.
Colours need to look pharmaceutical (green/white/maybe a bit of blue).
Text: Cannabidiol (CBD) Self-curing adhesive Polyethylene backing sheet.
Apply one patch to a smooth are of skin. Each patch can be worn for up to 24 hours. Apply subsequent patches to different areas to allow the skin to breathe between uses.
Do not apply to broken or irritable skin. Consult a doctor if you are taking medications or have medical conditions before using this or any other supplement. Do not use if you are pregnant or breastfeeding.
Store in a cool, dry place out of direct sunlight. Stable for three years. Once opened, use within 12 months.

```html
<!DOCTYPE html>
<html lang="en">
<head>
<meta charset="utf-8">
<title>CBD Patch Box – Dieline Artwork</title>
<link href="https://fonts.googleapis.com/css2?family=Outfit:wght@400;500;600;700&display=swap" rel="stylesheet">
<style>
  :root {
    --leaf: #8ca646;
    --ocean: #1f6ea3;
    --ink: #3a3a3a;
    --paper: #ffffff;
    --cutline: #2a2a2a;
    --backdrop: #ffffff;
  }
  * { margin: 0; padding: 0; box-sizing: border-box; }
  html, body {
    width: 1200px; height: 1000px; overflow: hidden;
    background: var(--backdrop);
    font-family: "Outfit", sans-serif;
  }
  .canvas { position: relative; width: 1200px; height: 1000px; }

  .dieline {
    position: absolute; top: 58px;
    width: 504px; height: 884px;
  }
  .dieline--inside { left: 70px; }
  .dieline--outside { left: 630px; }
  .dieline svg.cut { position: absolute; inset: 0; width: 504px; height: 884px; }
  .cut path, .cut line { fill: var(--paper); stroke: var(--cutline); stroke-width: 0.6; }
  .cut line { fill: none; }

  /* printable panel: x 104–398, y 164–460 */
  .panel {
    position: absolute; left: 104px; top: 164px;
    width: 294px; height: 296px;
  }

  /* back panel copy */
  .info { padding: 16px 18px 0 20px; color: var(--ink); font-size: 12.4px; line-height: 1.3; }
  .info p { margin-bottom: 14px; }
  .info .label { color: var(--leaf); font-weight: 500; }
  .storage {
    position: relative; margin: 0 2px 0 2px; height: 56px;
  }
  .storage__shadow {
    position: absolute; inset: 4px -2px -4px 2px;
    background: var(--ocean); border-radius: 14px;
    transform: skewY(-1.5deg);
  }
  .storage__box {
    position: absolute; inset: 0;
    background: var(--leaf); border-radius: 14px;
    color: #fff; font-size: 11.6px; line-height: 1.25; text-align: center;
    display: flex; align-items: center; justify-content: center; padding: 0 8px;
  }

  /* front panel (printed upside down on the flat) */
  .front { transform: rotate(180deg); overflow: hidden; }
  .front .arcs { position: absolute; inset: 0; width: 294px; height: 296px; }
  .brand {
    position: absolute; left: 22px; top: 34px;
    display: flex; align-items: center; gap: 6px;
    color: var(--leaf); font-weight: 600; font-size: 11px; letter-spacing: 0.08em;
  }
  .brand__dot { width: 16px; height: 16px; border-radius: 50%; background: var(--leaf); }
  .product-name {
    position: absolute; left: 22px; top: 118px;
    color: var(--leaf); font-weight: 700; font-size: 36px; line-height: 1.05;
  }
  .product-spec {
    position: absolute; left: 22px; top: 210px;
    color: var(--ocean); font-weight: 400; font-size: 15px; line-height: 1.35;
  }
</style>
</head>
<body>
<main class="canvas">

  <!-- inside / back print -->
  <section class="dieline dieline--inside">
    <svg class="cut" viewBox="0 0 252 442" aria-hidden="true">
      <path d="M52,82 V20 H97 A22.5,20 0 0 1 142,20 H199 V82 Z"/>
      <path d="M52,82 H199 V372 H52 Z"/>
      <path d="M52,234 H32 Q0,234 0,272 V370 H52 Z"/>
      <path d="M199,234 H220 Q252,234 252,272 V370 H199 Z"/>
      <path d="M52,372 V382 H65 V440 H100 A20,20 0 0 1 140,440 H185 V382 H199 V372 Z"/>
      <line x1="52" y1="230" x2="199" y2="230"/>
      <line x1="52" y1="304" x2="199" y2="304"/>
      <line x1="52" y1="382" x2="199" y2="382"/>
      <path d="M95,316 V319 H127 V316" fill="none"/>
      <line x1="16" y1="308" x2="37" y2="320"/>
      <line x1="16" y1="332" x2="37" y2="320"/>
      <line x1="236" y1="308" x2="215" y2="320"/>
      <line x1="236" y1="332" x2="215" y2="320"/>
    </svg>
    <div class="panel">
      <div class="info">
        <p><span class="label">Direction:</span> Apply one patch to a smooth are of skin. Each patch can be worn for up to 24 hours. Apply subsequent patches to different areas to allow the skin to breathe between uses.</p>
        <p><span class="label">Description:</span> Do not apply to broken or irritable skin. Consult a doctor if you are taking medications or have medical conditions before using this or any other supplement. Do not use if you are pregnant or breastfeeding.</p>
        <div class="storage">
          <div class="storage__shadow"></div>
          <div class="storage__box">Store in a cool, dry place out of direct sunlight. Stable for three years. Once opened, use within 12 months.</div>
        </div>
      </div>
    </div>
  </section>

  <!-- outside / front print -->
  <section class="dieline dieline--outside">
    <svg class="cut" viewBox="0 0 252 442" aria-hidden="true">
      <path d="M52,82 V20 H97 A22.5,20 0 0 1 142,20 H199 V82 Z"/>
      <path d="M52,82 H199 V372 H52 Z"/>
      <path d="M52,234 H32 Q0,234 0,272 V370 H52 Z"/>
      <path d="M199,234 H220 Q252,234 252,272 V370 H199 Z"/>
      <path d="M52,372 V382 H65 V440 H100 A20,20 0 0 1 140,440 H185 V382 H199 V372 Z"/>
      <line x1="52" y1="230" x2="199" y2="230"/>
      <line x1="52" y1="304" x2="199" y2="304"/>
      <line x1="52" y1="382" x2="199" y2="382"/>
      <path d="M95,316 V319 H127 V316" fill="none"/>
      <line x1="16" y1="308" x2="37" y2="320"/>
      <line x1="16" y1="332" x2="37" y2="320"/>
      <line x1="236" y1="308" x2="215" y2="320"/>
      <line x1="236" y1="332" x2="215" y2="320"/>
    </svg>
    <div class="panel front">
      <svg class="arcs" viewBox="0 0 294 296" aria-hidden="true">
        <circle cx="398" cy="200" r="118" fill="none" stroke="var(--ocean)" stroke-width="6"/>
        <circle cx="404" cy="206" r="114" fill="none" stroke="var(--leaf)" stroke-width="8"/>
      </svg>
      <div class="brand"><span class="brand__dot"></span>VERDALIS</div>
      <h1 class="product-name">Cannabidiol<br>(CBD)</h1>
      <p class="product-spec">Self-curing adhesive<br>Polyethylene backing sheet</p>
    </div>
  </section>

</main>
</body>
</html>
```